We need UI/UX design for a public, informational website for The Copper Lantern.
The pages, structure, and content scope are already defined. Designers are required to work only on the UI/UX layout of these existing pages, focusing on clarity, hierarchy, spacing, and usability. Do not add, remove, rename, or reinterpret pages or content.
The website is strictly informational only. It must not include accounts, onboarding, payments, custody, escrow administration, marketplaces, dashboards, or any transactional functionality.
Scope of work
Apply UI/UX design to the predefined website pages
Design layout for text, images, notices, and sections
Ensure consistent components and layout patterns across page types
Optimize layouts for long form, compliance focused content
Content writing, page creation, and branding changes are out of scope.
Structure reference
The complete page list, hierarchy, and content definitions are provided in the technical documentation and must be treated as the primary source of truth.
A Figma link is provided only as a light visual reference for page existence and structure:
https://meadow-knot-48203956.plumsite.example/
Designers must rely on the documentation for in depth and authoritative reference.
Brand guidelines
The Copper Lantern has existing brand guidelines and official logos, including light and dark versions. These assets will be provided and must be followed exactly. Designers must not redesign, alter, or reinterpret the brand identity.
Look and feel direction
The desired visual direction is inspired by:
https://ledgerwaltz.example/
This reference is provided only to indicate:
Institutional and enterprise tone
Clean, modern typography
Strong hierarchy and generous whitespace
Editorial, content first layouts
Do not copy branding, layouts, components, or assets from the reference site.
Hero section direction
The hero section should follow a similar structural approach to the hero used on https://ledgerwaltz.example/
, meaning:
Strong editorial framing
Clear headline hierarchy
Calm, institutional first impression
However, the background video must be Abu Dhabi focused, not generic or global. The video should visually reflect:
Abu Dhabi skyline or architectural language
Institutional, sovereign, long term infrastructure tone
Clean, slow, cinematic motion
No promotional, marketing, or lifestyle visuals
The hero must remain informational, restrained, and credible. No hype. No calls to invest. No implied participation.
Constraints
One global primary CTA only: “Continue to Halvemark” (external)
All other interactions must be informational
No visuals or language implying offers, investment, eligibility, or participation
Clear separation between informational content and any external operational platforms
Deliverables
High fidelity UI/UX designs created in Figma, covering:
Desktop layouts
Tablet layouts where relevant
Mobile layouts
Complete Figma file(s) including:
All designed pages defined in the technical documentation
A reusable component library (headers, footers, cards, notice panels, forms, CTAs, typography styles, spacing system)
Clearly defined layout grids, spacing rules, and text styles
Proper use of components and variants, not detached frames
Designs prepared for developer handoff, including:
Clear layer naming and structure
Auto layout where appropriate
Consistent use of styles and components
Responsive behavior demonstrated within Figma
Notes or annotations only where necessary for clarity
No prototypes, interactions, or motion design beyond basic layout states, unless explicitly requested. The focus is static UI/UX clarity, not animation.
A detailed technical specification document and official brand assets will be provided.
Any designs delivered outside Figma, that alter structure or content, or that ignore the defined constraints, boundaries, or tone will be rejected.

```html
<!DOCTYPE html>
<html lang="en">
<head>
<meta charset="utf-8">
<title>The Copper Lantern — Governance Framework</title>
<link href="https://fonts.googleapis.com/css2?family=Manrope:wght@400;500;600&display=swap" rel="stylesheet">
<style>
:root{
  --backdrop:#b3b3b3;
  --ink:#111111;
  --black:#000000;
  --white:#ffffff;
  --paper:#f4f4f4;
  --muted:#6b6b6b;
  --soft-line:#d6d6d6;
  --sky:#4fb3f6;
  --dark-line:rgba(255,255,255,.18);
  --on-dark-muted:rgba(255,255,255,.62);
}
*{box-sizing:border-box;margin:0;padding:0}
html,body{width:1200px;height:3665px;overflow:hidden}
body{background:var(--backdrop);font-family:"Manrope",Arial,sans-serif;color:var(--ink)}
.page{position:absolute;left:81px;top:81px;width:1038px;height:3505px;background:var(--paper);overflow:hidden}
.abs{position:absolute}
svg{display:block}

/* hero */
.hero{left:0;top:0;width:1038px;height:1069px;background:var(--black)}
.hero-photo{left:0;top:0}
.nav{left:176px;top:50px;width:685px;height:30px;background:var(--white);border-radius:15px;display:flex;align-items:center;font-size:9px;font-weight:500}
.nav a{color:var(--ink);text-decoration:none;position:absolute}
.nav .cta{background:var(--black);color:var(--white);padding:5px 8px;border-radius:10px;font-size:8.5px}
.brand{left:427px;top:14px;width:94px;height:94px;border-radius:50%;background:var(--white);display:flex;align-items:center;justify-content:center;text-align:center;font-size:10px;font-weight:600;letter-spacing:.06em;line-height:1.25;color:var(--ink)}
.hero-title{left:0;width:1038px;top:244px;text-align:center;color:var(--white);font-size:40px;font-weight:500;line-height:50px;letter-spacing:-.01em}
.hero-sub{left:0;width:1038px;top:356px;text-align:center;color:rgba(255,255,255,.88);font-size:17px;line-height:26px}
.pill{display:inline-block;background:var(--white);color:var(--ink);border-radius:14px;font-size:10.5px;font-weight:600;text-decoration:none;text-align:center}
.hero-btn{left:447px;top:424px;width:143px;height:26px;line-height:26px}
.scroll-cue{left:506px;top:613px;width:26px;height:26px;border-radius:50%;background:#3a3a3a;display:flex;align-items:center;justify-content:center}

.about-label{left:148px;top:730px;color:var(--white);font-size:9px}
.about-title{left:148px;top:746px;color:var(--white);font-size:27px;font-weight:500;line-height:32px;width:360px}
.about-text{left:148px;top:848px;width:356px;color:rgba(255,255,255,.8);font-size:8.6px;line-height:14.5px}
.about-btn{left:148px;top:919px;width:113px;height:24px;line-height:24px}
.gallery{left:532px;top:726px;width:362px;height:222px;border:1.5px solid #5a5a5a;border-radius:14px;padding:4px;display:flex;gap:3px}
.gallery-panel{flex:1;border-radius:10px;position:relative}
.gallery-panel span{position:absolute;left:14px;bottom:16px;color:var(--white);font-size:10px;line-height:12px}

/* role */
.role-curve{left:0;top:971px}
.role-label{left:0;width:1038px;top:1145px;text-align:center;font-size:9px}
.role-title{left:0;width:1038px;top:1160px;text-align:center;font-size:27px;font-weight:500}
.role-card{top:1210px;width:231px;height:315px;background:var(--white);border:1.5px solid var(--ink);border-radius:10px;overflow:hidden}
.role-card .photo{height:142px}
.role-card h3{font-size:17px;font-weight:500;margin:16px 18px 6px}
.role-card p{font-size:8.4px;line-height:13px;color:var(--muted);margin:0 18px;height:46px}
.meta{margin:4px 18px 0;font-size:8.4px}
.meta div{display:flex;height:23px;align-items:center}
.meta dt{width:59px;color:var(--muted)}
.meta dd{font-weight:600}

/* framework */
.framework{left:0;top:1616px}
.fw-label{left:148px;top:1692px;color:var(--white);font-size:9px}
.fw-title{left:148px;top:1708px;color:var(--white);font-size:27px;font-weight:500}
.fw-desc{left:148px;top:1760px;width:230px;color:rgba(255,255,255,.85);font-size:8.6px;line-height:15px}
.fw-list{left:467px;top:1688px;width:420px;list-style:none}
.fw-item{height:100px;border-bottom:1px solid var(--dark-line);color:var(--white)}
.fw-item:last-child{border-bottom:none}
.fw-item .num{font-size:8px;color:var(--on-dark-muted);display:block;height:12px}
.fw-item h4{font-size:17px;font-weight:500;line-height:24px}
.fw-item p{font-size:8.4px;line-height:13px;color:var(--on-dark-muted);margin-top:2px}

/* reviewers */
.reviewers-bg{left:0;top:2168px;width:1038px;height:470px;background:var(--white)}
.rev-title{left:0;width:1038px;top:2346px;text-align:center;font-size:27px;font-weight:500}
.rev-card{top:2403px;width:171px;height:145px;background:var(--white);border:1px solid #bdbdbd;border-radius:8px;padding:22px 20px}
.rev-card h4{font-size:12.5px;font-weight:500;line-height:17px}
.rev-card p{font-size:8.2px;line-height:12.5px;color:var(--muted);margin-top:8px}

/* why */
.why-curve{left:0;top:2622px}
.why-title{left:0;width:1038px;top:2702px;text-align:center;font-size:27px;font-weight:500}
.why-item{width:340px;text-align:center}
.why-item h4{font-size:13px;font-weight:500}
.why-item p{font-size:8.4px;line-height:13px;color:var(--muted);margin-top:6px}

/* cta */
.cta-curve{left:0;top:2972px}
.cta-label{left:0;width:1038px;top:3053px;text-align:center;color:#e9f5ff;font-size:8.5px;letter-spacing:.04em}
.cta-title{left:0;width:1038px;top:3074px;text-align:center;font-size:25px;font-weight:500;line-height:29px;color:#0d1a2a;text-transform:uppercase}
.cta-text{left:0;width:1038px;top:3141px;text-align:center;font-size:10.5px;line-height:16px;color:#102437}
.cta-btn{left:419px;top:3182px;width:190px;height:26px;line-height:26px;background:var(--black);color:var(--white);border-radius:13px;font-size:10.5px;font-weight:600;text-align:center}

/* footer */
.footer{left:0;top:3267px;width:1038px;height:238px;background:var(--black);color:var(--white)}
.foot-col{top:28px;font-size:8.6px}
.foot-col h5{font-size:9px;font-weight:500;margin-bottom:9px}
.foot-col li{list-style:none;color:rgba(255,255,255,.75);font-size:7.6px;line-height:15.2px}
.foot-col p{color:rgba(255,255,255,.75);font-size:7.6px;line-height:11px;width:150px}
.foot-rule{left:191px;top:158px;width:654px;height:1px;background:rgba(255,255,255,.15)}
.foot-legal{left:191px;top:177px;width:680px;font-size:7.2px;line-height:11px;color:rgba(255,255,255,.65)}
</style>
</head>
<body>
<main class="page">

  <section class="hero abs">
    <svg class="hero-photo abs" width="1038" height="620" role="img" aria-label="Photograph of a dense city skyline with towers and highways at dusk">
      <defs>
        <linearGradient id="heroFill" x1="0" y1="0" x2="0" y2="1">
          <stop offset="0" stop-color="#4a4c4f"/>
          <stop offset=".55" stop-color="#3a3b3d"/>
          <stop offset="1" stop-color="#202122"/>
        </linearGradient>
      </defs>
      <path d="M0 0H1038V505Q519 655 0 505Z" fill="url(#heroFill)"/>
    </svg>

    <nav class="nav abs">
      <a style="left:20px">Home</a>
      <a style="left:64px">Framework</a>
      <a style="left:133px">Projects</a>
      <a style="left:186px">Company</a>
      <a style="left:466px">Insights</a>
      <a style="left:518px">Contact</a>
      <a class="cta" style="left:578px">Continue to Halvemark</a>
    </nav>
    <div class="brand abs">THE COPPER<br>LANTERN</div>

    <h1 class="hero-title abs">A Governance Framework for<br>Structured Project Oversight</h1>
    <p class="hero-sub abs">Clear boundaries. Institutional discipline. Transparent<br>structures for managing risk and accountability.</p>
    <a class="pill hero-btn abs">Learn the Framework</a>
    <div class="scroll-cue abs">
      <svg width="10" height="8" viewBox="0 0 10 8"><path d="M1 1H9L5 7Z" fill="none" stroke="#fff" stroke-width="1.2"/></svg>
    </div>

    <p class="about-label abs">About The Copper Lantern</p>
    <h2 class="about-title abs">From Governance Frameworks to Intelligent Infrastructure</h2>
    <p class="about-text abs">The Copper Lantern is a governance and project origination group focused on defining structural standards for complex initiatives. We publish clear frameworks that explain role separation, accountability, and long-term oversight across governance, operations, and project-level execution.</p>
    <a class="pill about-btn abs">Our Framework</a>

    <div class="gallery abs">
      <div class="gallery-panel" role="img" aria-label="Monochrome photograph of tall twin towers" style="background:linear-gradient(160deg,#5c5c5c,#2a2a2a)"><span>Clear Role<br>Separation</span></div>
      <div class="gallery-panel" role="img" aria-label="Monochrome photograph of a city skyline" style="background:linear-gradient(180deg,#565656,#262626)"><span>Independent<br>Oversight<br>Principles</span></div>
      <div class="gallery-panel" role="img" aria-label="Monochrome photograph looking up at a tower" style="background:linear-gradient(200deg,#666,#2c2c2c)"><span>Institutional-Grade<br>Standards</span></div>
    </div>
  </section>

  <svg class="role-curve abs" width="1038" height="100"><path d="M0 0H1038Q519 196 0 0Z" fill="#000"/></svg>

  <section>
    <p class="role-label abs">Role Clarity</p>
    <h2 class="role-title abs">Understanding Our Role</h2>

    <article class="role-card abs" style="left:148px">
      <div class="photo" role="img" aria-label="Monochrome photograph of a curved glass tower" style="background:linear-gradient(180deg,#d9d9d9,#6e6e6e)"></div>
      <h3>Governance</h3>
      <p>We define structural frameworks, role boundaries, and oversight mechanisms. This is our domain.</p>
      <dl class="meta">
        <div><dt>Category</dt><dd>Governance Framework</dd></div>
        <div><dt>Audience</dt><dd>Institutional &amp; Public Reference</dd></div>
        <div><dt>Disclosure</dt><dd>Informational Use Only *</dd></div>
      </dl>
    </article>
    <article class="role-card abs" style="left:403px">
      <div class="photo" role="img" aria-label="Monochrome aerial photograph of city blocks and roads" style="background:linear-gradient(160deg,#9a9a9a,#3d3d3d)"></div>
      <h3>Operations</h3>
      <p>Day-to-day execution and project management occur outside our organization, through Halvemark.</p>
      <dl class="meta">
        <div><dt>Category</dt><dd>Governance Framework</dd></div>
        <div><dt>Audience</dt><dd>Institutional &amp; Public Reference</dd></div>
        <div><dt>Disclosure</dt><dd>Informational Use Only *</dd></div>
      </dl>
    </article>
    <article class="role-card abs" style="left:658px">
      <div class="photo" role="img" aria-label="Monochrome photograph of a curved waterfront hotel complex" style="background:linear-gradient(180deg,#e2e2e2,#5a5a5a)"></div>
      <h3>Transactions</h3>
      <p>We do not facilitate, execute, or participate in any financial transactions or operational activities.</p>
      <dl class="meta">
        <div><dt>Category</dt><dd>Governance Framework</dd></div>
        <div><dt>Audience</dt><dd>Institutional &amp; Public Reference</dd></div>
        <div><dt>Disclosure</dt><dd>Informational Use Only *</dd></div>
      </dl>
    </article>
  </section>

  <svg class="framework abs" width="1038" height="654" role="img" aria-label="Muted aerial photograph of a marina district with high-rise towers">
    <defs>
      <linearGradient id="fwFill" x1="0" y1="0" x2="0" y2="1">
        <stop offset="0" stop-color="#4b4b4b"/>
        <stop offset=".5" stop-color="#3c3d3e"/>
        <stop offset="1" stop-color="#2b2c2d"/>
      </linearGradient>
    </defs>
    <path d="M0 0H1038V552Q519 752 0 552Z" fill="url(#fwFill)"/>
  </svg>
  <p class="fw-label abs">Core Governance Principles</p>
  <h2 class="fw-title abs">The Framework</h2>
  <p class="fw-desc abs">A structured set of principles defining oversight, accountability, and role separation.</p>
  <ol class="fw-list abs">
    <li class="fw-item"><span class="num">01</span><h4>Role Boundaries</h4><p>Clear separation between governance responsibilities, operational platforms, and project-level execution to prevent overlap and ambiguity.</p></li>
    <li class="fw-item"><span class="num">02</span><h4>SPV Structure</h4><p>Ring-fenced project structures designed to isolate liability, clarify accountability, and support disciplined execution.</p></li>
    <li class="fw-item"><span class="num">03</span><h4>Escrow Model</h4><p>Independent escrow principles describing conditional release mechanisms and third-party oversight—without operational execution on this site.</p></li>
    <li class="fw-item"><span class="num">04</span><h4>Records and Registers</h4><p>Standards for documentation, evidence records, and transparency to support auditability and structural clarity.</p></li>
    <li class="fw-item"><span class="num">05</span><h4>Risk and Boundaries</h4><p>Defined limitation frameworks outlining scope, risk containment, and enforcement of governance boundaries.</p></li>
  </ol>

  <div class="reviewers-bg abs"></div>
  <svg class="abs" style="left:0;top:2168px" width="1038" height="102"><path d="M0 0H1038Q519 200 0 0Z" fill="#2b2c2d"/></svg>
  <h2 class="rev-title abs">For Framework Reviewers</h2>
  <article class="rev-card abs" style="left:148px"><h4>Review Governance Structures</h4><p>Explore published frameworks outlining governance models, role separation, and accountability principles.</p></article>
  <article class="rev-card abs" style="left:339px"><h4>Defined Structural Ownership</h4><p>Frameworks clarify responsibility and authority boundaries without operational or transactional execution.</p></article>
  <article class="rev-card abs" style="left:530px"><h4>Operational Independence</h4><p>Execution, asset handling, and platform operations occur outside this site through independent entities.</p></article>
  <article class="rev-card abs" style="left:721px"><h4>Clear Access Boundaries</h4><p>This site provides documentation and reference materials only—no onboarding, custody, or execution.</p></article>

  <svg class="why-curve abs" width="1038" height="360"><path d="M0 108Q519 -108 1038 108V360H0Z" fill="#f4f4f4"/></svg>
  <h2 class="why-title abs">Why The Copper Lantern</h2>
  <div class="why-item abs" style="left:157px;top:2770px"><h4>Governance-First Approach</h4><p>We prioritize structural clarity and accountability, treating governance as the foundation—not an afterthought.</p></div>
  <div class="why-item abs" style="left:539px;top:2770px"><h4>Proven Structural Principles</h4><p>Our frameworks are informed by institutional standards across governance, compliance, and long-term infrastructure design.</p></div>
  <div class="why-item abs" style="left:157px;top:2849px"><h4>Bridging Structure &amp; Execution</h4><p>We define governance and role boundaries while execution occurs independently through separate operational platforms.</p></div>
  <div class="why-item abs" style="left:539px;top:2849px"><h4>Defined Control &amp; Boundaries</h4><p>Clear limitations ensure responsibilities remain properly scoped, auditable, and enforceable.</p></div>

  <svg class="cta-curve abs" width="1038" height="296"><path d="M0 106Q519 -106 1038 106V296H0Z" fill="#4fb3f6"/></svg>
  <p class="cta-label abs">FOR PROJECT ORIGINATORS</p>
  <h2 class="cta-title abs">Define Your Project’s<br>Governance Framework</h2>
  <p class="cta-text abs">Design clear structural roles, accountability boundaries, and oversight<br>principles before operational execution begins.</p>
  <a class="cta-btn abs">Start a Framework Discussion</a>

  <footer class="footer abs">
    <div class="foot-col abs" style="left:191px"><h5>The Copper Lantern</h5><p>A governance framework for structured project oversight and risk management.</p></div>
    <div class="foot-col abs" style="left:359px"><h5>Framework</h5><ul><li>Role Boundaries</li><li>SPV Structure</li><li>Escrow Model</li><li>Records and Registers</li><li>Risk and Boundaries</li></ul></div>
    <div class="foot-col abs" style="left:527px"><h5>Company</h5><ul><li>About</li><li>Leadership</li><li>Governance</li><li>Press</li><li>Careers</li><li>Contact</li></ul></div>
    <div class="foot-col abs" style="left:696px"><h5>Legal</h5><ul><li>Terms of Use</li><li>Privacy Policy</li><li>Cookie Policy</li><li>Disclaimer and Risk Notices</li><li>Acceptable Use</li><li>Accessibility</li></ul></div>
    <div class="foot-rule abs"></div>
    <p class="foot-legal abs">© 2026 The Copper Lantern. All rights reserved.<br><br>This website provides informational content only. The Copper Lantern does not provide investment advice, execute projects, or facilitate transactions. All operational activities are conducted through Halvemark, a separate platform.</p>
  </footer>
</main>
</body>
</html>
```